Unique Business Card Design

Unique Business Card design for our orthotic and prosthetic company. Our logo is on our website, color is light blue. Unique shape (artificial leg shaped, vertical, etc..) preferred. Logo, business name, individual name and basic demographics needed.

Industry/Entity Type

Business

Contact Information for Business Card

Logo, Industry, Phone # Logo, "Prosthetic & Orthotic Services" Place to add individual name and contact info

Colors
cee9f5

Requirements
Must have
• The icon must be there, placement of "Prosthetic & Orthotic Services" can be moved
Nice to have
• Like the mix of light blue, and a little darker blue. One design included the icons from my website which was a nice touch

```html
<!DOCTYPE html>
<html lang="en">
<head>
<meta charset="utf-8">
<title>Limbwell Inc – Business Cards</title>
<link rel="stylesheet" href="https://fonts.googleapis.com/css2?family=PT+Sans:wght@400;700&family=Crimson+Text:ital@1&display=swap">
<style>
  :root {
    --sky: #cfe8f5;
    --blue: #0b70d4;
    --ink: #111418;
    --white: #ffffff;
    --page: #eef1f4;
    --sans: "PT Sans", Arial, sans-serif;
    --serif: "Crimson Text", Georgia, serif;
  }
  * { box-sizing: border-box; margin: 0; padding: 0; }
  html, body { width: 1200px; height: 900px; overflow: hidden; }
  body { background: var(--page); position: relative; font-family: var(--sans); }

  .card { position: absolute; overflow: hidden; box-shadow: 0 6px 18px rgba(0,0,0,.18); }
  .card-front { left: 78px; top: 35px; width: 587px; height: 362px; background: var(--sky); }
  .card-back { left: 388px; top: 505px; width: 567px; height: 352px; background: var(--blue); }

  .card-bands { position: absolute; inset: 0; }

  .brand-mark { position: absolute; border-radius: 50%; }
  .card-front .brand-mark { left: 91px; top: 52px; width: 106px; height: 106px; background: var(--blue); }
  .card-back .brand-mark { left: 73px; top: 125px; width: 110px; height: 110px; background: var(--white); }

  .brand-name {
    position: absolute; font-weight: 400; font-size: 33px; letter-spacing: .3px;
    line-height: 1; padding-bottom: 5px; white-space: nowrap;
  }
  .card-front .brand-name { left: 224px; top: 70px; width: 272px; color: var(--blue); border-bottom: 2px solid var(--blue); }
  .card-back .brand-name { left: 212px; top: 140px; width: 280px; color: var(--white); border-bottom: 2px solid var(--white); }

  .tagline { position: absolute; font-family: var(--serif); font-style: italic; font-size: 18px; white-space: nowrap; }
  .card-front .tagline { left: 224px; top: 112px; width: 272px; text-align: center; color: var(--blue); }
  .card-back .tagline { left: 212px; top: 185px; width: 280px; text-align: center; color: var(--white); }

  .emboss-circle {
    position: absolute; left: 115px; top: 5px; width: 340px; height: 340px; border-radius: 50%;
    border: 2px solid rgba(0,40,110,.18); background: rgba(255,255,255,.04);
  }

  .person { position: absolute; right: 315px; top: 259px; text-align: right; color: var(--white); }
  .person-name { font-size: 20px; font-weight: 700; line-height: 1.15; }
  .person-role { font-size: 16px; line-height: 1.25; }

  .contact-list { position: absolute; left: 294px; top: 249px; list-style: none; color: var(--white); font-size: 16px; }
  .contact-list li { display: flex; align-items: center; height: 21px; }
  .contact-list svg { width: 12px; height: 12px; margin-right: 12px; fill: var(--white); }

  .address { position: absolute; left: 103px; top: 321px; color: var(--white); font-size: 16px; white-space: nowrap; }
</style>
</head>
<body>

  <section class="card card-front" aria-label="Business card front">
    <svg class="card-bands" width="587" height="362" viewBox="0 0 587 362" aria-hidden="true">
      <polygon points="0,198 484,198 459,225 0,225" fill="var(--ink)"/>
      <polygon points="0,228 461,228 493,190 587,190 587,362 0,362" fill="var(--blue)"/>
    </svg>
    <span class="brand-mark" aria-hidden="true"></span>
    <div class="brand-name">LIMBWELL INC</div>
    <div class="tagline">Prosthetic &amp; Orthotic Services</div>

    <div class="person">
      <div class="person-name">Daniel Harper</div>
      <div class="person-role">Managing Director</div>
    </div>

    <ul class="contact-list">
      <li><svg viewBox="0 0 24 24" aria-hidden="true"><path d="M6.6 10.8a15.1 15.1 0 0 0 6.6 6.6l2.2-2.2a1 1 0 0 1 1-.25 11.4 11.4 0 0 0 3.6.57 1 1 0 0 1 1 1V20a1 1 0 0 1-1 1A17 17 0 0 1 3 4a1 1 0 0 1 1-1h3.5a1 1 0 0 1 1 1c0 1.25.2 2.45.57 3.57a1 1 0 0 1-.25 1z"/></svg>(555) 014-2290</li>
      <li><svg viewBox="0 0 24 24" aria-hidden="true"><path d="M2 5h20v14H2zm2 2v.5l8 5 8-5V7zm0 3v7h16v-7l-8 5z"/></svg>info@limbwellinc.com</li>
      <li><svg viewBox="0 0 24 24" aria-hidden="true"><path d="M12 2a10 10 0 1 0 0 20 10 10 0 0 0 0-20zm6.9 6h-3a15 15 0 0 0-1.3-3.9A8 8 0 0 1 18.9 8zM12 4c.8 1.2 1.5 2.5 1.9 4h-3.8c.4-1.5 1.1-2.8 1.9-4zM4.3 14a8 8 0 0 1 0-4h3.4a16 16 0 0 0 0 4zm.8 2h3a15 15 0 0 0 1.3 3.9A8 8 0 0 1 5.1 16zm3-8h-3a8 8 0 0 1 4.3-3.9A15 15 0 0 0 8.1 8zM12 20c-.8-1.2-1.5-2.5-1.9-4h3.8c-.4 1.5-1.1 2.8-1.9 4zm2.3-6H9.7a14 14 0 0 1 0-4h4.6a14 14 0 0 1 0 4zm.3 5.9a15 15 0 0 0 1.3-3.9h3a8 8 0 0 1-4.3 3.9zm1.7-5.9a16 16 0 0 0 0-4h3.4a8 8 0 0 1 0 4z"/></svg>www.limbwellinc.com</li>
    </ul>

    <div class="address">12345, Address Goes Here Country Name, 123456.</div>
  </section>

  <section class="card card-back" aria-label="Business card back">
    <span class="emboss-circle" aria-hidden="true"></span>
    <span class="brand-mark" aria-hidden="true"></span>
    <div class="brand-name">LIMBWELL INC</div>
    <div class="tagline">Prosthetic &amp; Orthotic Services</div>
  </section>

</body>
</html>
```